Calvanto Group Real Estate Company business cards

New business card design, we are generally happy with the basic layout of the existing front of business card, (feel free to change) but require a head shot photo on the back side.

http://www.calvanto.com.au/

Attached logos, and existing business card

------------------------------

Target Market(s)

Real estate

Industry/Entity Type

Real Estate

Contact Information for Business Card

Standard size double sided

Font styles to use
Other font styles liked:
• Futura

Requirements
Must have
• Photo head shot on the back side
Nice to have
• yes
Should not have
• No

```html
<!DOCTYPE html>
<html lang="en">
<head>
<meta charset="utf-8">
<title>Calvanto Group – Business Cards</title>
<link href="https://fonts.googleapis.com/css2?family=Jost:wght@400;500&display=swap" rel="stylesheet">
<style>
  :root {
    --stage: #e9e7e4;
    --card: #121212;
    --card-edge: #1c1c1c;
    --purple: #3b2a7e;
    --orange: #f39019;
    --white: #f2f2f2;
    --grey: #8d8d8d;
    --photo-top: #2a3550;
    --photo-bottom: #141a2a;
  }
  * { box-sizing: border-box; margin: 0; padding: 0; }
  html, body { width: 1200px; height: 814px; overflow: hidden; }
  body {
    background: var(--stage);
    font-family: "Jost", "Futura", sans-serif;
    position: relative;
  }
  .card {
    position: absolute;
    width: 540px;
    height: 310px;
    background: var(--card);
    border: 1px solid var(--card-edge);
    box-shadow: 0 10px 24px rgba(0,0,0,.25);
    overflow: hidden;
  }
  .card--front { left: 45px; top: 252px; }
  .card--back  { left: 615px; top: 252px; }

  /* Front */
  .brand {
    position: absolute;
    left: 128px; top: 52px;
    display: flex; align-items: center; gap: 10px;
  }
  .brand__mark { width: 14px; height: 14px; background: var(--purple); }
  .brand__name {
    font-size: 54px; font-weight: 500; color: var(--purple);
    letter-spacing: -0.5px; line-height: 1;
  }
  .tagline {
    position: absolute; left: 205px; top: 122px;
    font-size: 14px; color: var(--purple); word-spacing: 4px;
  }
  .divider {
    position: absolute; left: 262px; top: 180px;
    width: 1px; height: 90px; background: var(--grey);
  }
  .person {
    position: absolute; right: 288px; top: 208px;
    text-align: right; line-height: 1.15;
  }
  .person__name { font-size: 19px; color: var(--purple); font-weight: 500; }
  .person__role { font-size: 15px; color: var(--orange); }
  .person__company { font-size: 15px; color: var(--white); }
  .contact {
    position: absolute; left: 278px; top: 176px;
    list-style: none; font-size: 13px; color: var(--white); line-height: 1.35;
  }
  .contact li { display: flex; align-items: center; gap: 8px; height: 19px; }
  .contact svg { width: 11px; height: 11px; fill: var(--grey); flex: none; }
  .contact .no-icon { padding-left: 0; }

  /* Back */
  .headshot {
    position: absolute; left: 92px; top: 70px;
    width: 240px; height: 240px;
    background: linear-gradient(180deg, var(--photo-top), var(--photo-bottom));
  }
  .back-brand {
    position: absolute; left: 356px; top: 108px;
    display: flex; align-items: center; gap: 8px;
  }
  .back-brand__mark { width: 12px; height: 12px; background: var(--orange); }
  .back-brand__name { font-size: 34px; font-weight: 500; color: var(--orange); line-height: 1; }
  .back-web {
    position: absolute; left: 366px; top: 160px;
    font-size: 13px; color: var(--white); letter-spacing: .3px;
  }
</style>
</head>
<body>
  <section class="card card--front">
    <div class="brand">
      <span class="brand__mark"></span>
      <span class="brand__name">calvanto</span>
    </div>
    <p class="tagline">Buy | Sell | Rent</p>

    <div class="person">
      <p class="person__name">Daniel Tran</p>
      <p class="person__role">Director</p>
      <p class="person__company">Calvanto Group</p>
    </div>
    <div class="divider"></div>

    <ul class="contact">
      <li class="no-icon">ABN: 41 258 903 617</li>
      <li>
        <svg viewBox="0 0 12 12"><path d="M2.5 1l2 2.2-1 1.3a7 7 0 0 0 4 4l1.3-1L11 9.5 9.6 11C5 11 1 7 1 2.4z"/></svg>
        0412 586 301
      </li>
      <li>
        <svg viewBox="0 0 12 12"><path d="M1 2.5h10v7H1z M1.5 3l4.5 3.4L10.5 3" stroke="#121212" stroke-width=".9"/></svg>
        daniel.tran@calvanto.com.au
      </li>
      <li>
        <svg viewBox="0 0 12 12"><circle cx="6" cy="6" r="5"/><path d="M1 6h10M6 1c2 2.5 2 7.5 0 10M6 1c-2 2.5-2 7.5 0 10" stroke="#121212" stroke-width=".8" fill="none"/></svg>
        www.calvanto.com.au
      </li>
    </ul>
  </section>

  <section class="card card--back">
    <div class="headshot" role="img" aria-label="Head-and-shoulders portrait photo of the director in a navy suit and blue tie"></div>
    <div class="back-brand">
      <span class="back-brand__mark"></span>
      <span class="back-brand__name">calvanto</span>
    </div>
    <p class="back-web">www.calvanto.com.au</p>
  </section>
</body>
</html>
```